Income Tax and Accounting Brochure

I need a brochure using my new logo (file attached). I do tax work and accounting work. I am an EA (QFB Enrolled Agent - logo attached) and would like this incorporated into the brochure. I also have a MSA in Accounting. Please incorporate the text that I have provided in the brochure.
Updates

Need extra days to review

Target Market(s)

Tax Clients - both business and individuals

Industry/Entity Type

Accounting

Colors
0054AA
0677BA
7BADD7
CADEEF
E8F1F8

Requirements
Must have
• Use my logo and the QFB EA file in the brochure
Nice to have
• I would like to see a brochure that I can customize with my own text if possible.

```html
<!DOCTYPE html>
<html lang="en">
<head>
<meta charset="utf-8">
<title>Ridgeline Accounting &amp; Consulting – Tri-fold Brochure</title>
<link href="https://fonts.googleapis.com/css2?family=Montserrat:wght@300;400;500;600;700;800&family=Oswald:wght@500&display=swap" rel="stylesheet">
<style>
:root{
  --navy:#1f3f9e;
  --blue:#0054aa;
  --sky:#7badd7;
  --red:#d01f3c;
  --ink:#2b2b2b;
  --paper:#ffffff;
  --stage:#eef0f3;
  --plum:#8c1d5a;
  --indigo:#2e3f9c;
}
*{margin:0;padding:0;box-sizing:border-box}
html,body{width:1200px;height:2527px;overflow:hidden;background:var(--stage)}
body{font-family:"Montserrat",Arial,sans-serif;color:var(--ink);position:relative}
.spread{position:absolute;left:30px;width:1140px;height:882px;display:flex;background:var(--paper);box-shadow:0 6px 24px rgba(0,0,0,.18);overflow:hidden}
.spread--outside{top:341px}
.spread--inside{top:1303px}
.panel{position:relative;width:380px;height:882px;overflow:hidden}
.abs{position:absolute}
.body-copy{font-size:13px;line-height:1.2;font-weight:400}
.dotted{height:0;border-top:2px dotted var(--red);position:absolute}
.dotted::after{content:"";position:absolute;left:50%;top:-3px;width:44px;height:4px;margin-left:-22px;background:var(--blue);border-radius:2px}
.photo{position:absolute}
/* outside left */
.about{left:36px;top:40px;width:300px}
.about .firm{color:var(--blue);font-weight:700;font-size:14px}
.mess-title{left:36px;top:160px;font-size:24px;font-weight:700;line-height:1.05}
.mess-title .r{color:var(--red)}
.mess-title .b{color:var(--blue)}
.mess-copy{left:36px;top:238px;width:310px}
/* outside middle */
.contact-head{left:0;width:380px;top:500px;text-align:center;font-size:35px;font-weight:700;color:var(--red)}
.contact-head span{color:var(--blue)}
.contact-icons{left:72px;top:566px;width:236px;display:flex;justify-content:space-between}
.contact-firm{left:0;width:380px;top:625px;text-align:center;font-family:"Oswald",Arial Narrow,sans-serif;font-weight:500;font-size:19px;color:var(--blue)}
.contact-line{left:0;width:380px;text-align:center;font-weight:500;font-size:14px;color:#222}
.contact-phone{font-size:20px;font-weight:600}
.social{left:146px;top:820px;display:flex;gap:22px}
.social i{display:block;width:20px;height:20px;border-radius:50%;background:var(--blue)}
.social i:nth-child(2){background:var(--red)}
.social i:nth-child(3){background:var(--sky)}
/* cover */
.brand{left:30px;top:58px;display:flex;align-items:center;gap:12px}
.brand-dot{width:72px;height:72px;border-radius:50%;background:var(--blue)}
.brand-name{color:var(--blue);font-weight:600;font-size:22px;letter-spacing:1.5px;line-height:1.45}
.brand-name small{display:block;font-size:17px;letter-spacing:4px}
.headline{left:0;width:380px;top:650px;text-align:center;font-weight:800;font-size:34px;line-height:1.02;color:var(--blue)}
.headline .red{color:var(--red)}
.tagline{left:0;width:380px;top:762px;text-align:center;font-size:17px;font-weight:500;line-height:1.15;color:#333}
.call-box{left:30px;width:312px;top:810px;height:37px;border:2.5px solid var(--red);border-radius:6px;text-align:center;font-size:26px;font-weight:700;color:var(--blue);line-height:32px;letter-spacing:.5px}
/* inside left */
.portrait{left:38px;top:36px;width:130px;height:130px;border-radius:50%;border:4px solid var(--blue)}
.person-name{right:24px;top:48px;text-align:right;color:var(--red);font-size:24px;font-weight:700;line-height:1.1}
.person-name small{display:block;color:var(--blue);font-size:16px;font-weight:500}
.bio-wrap{left:36px;top:122px;width:320px}
.bio-wrap .gap{float:left;width:140px;height:76px}
.joy{left:36px;top:418px;font-size:24px;font-weight:700;color:var(--red);line-height:1.2}
/* inside middle */
.panel--why{background:linear-gradient(180deg,var(--plum) 0%,#5a2a7c 50%,var(--indigo) 100%);color:#fff}
.kicker{left:30px;top:44px;color:var(--sky);font-size:21px;font-weight:600}
.why-title{left:30px;top:72px;font-size:29px;font-weight:700}
.why-copy{left:30px;top:132px;width:320px;font-weight:300}
.why-copy p+p{margin-top:20px}
.services-head{left:30px;top:424px;color:var(--sky);font-size:24px;font-weight:600}
.service{left:30px;width:330px}
.service h3{display:flex;align-items:center;gap:10px;font-size:20px;font-weight:600}
.service p{margin-top:14px;font-size:13px;font-weight:300;line-height:1.15}
/* inside right */
.gets-head{left:30px;top:410px;color:var(--red);font-size:24px;font-weight:700}
.gets{left:30px;width:320px;display:flex;gap:14px}
.gets svg{flex:none}
.gets p{font-size:13px;line-height:1.15}
.gets b{color:var(--blue);font-weight:600}
</style>
</head>
<body>

<!-- OUTSIDE SPREAD -->
<section class="spread spread--outside">
  <!-- About panel -->
  <div class="panel panel--about">
    <div class="abs about body-copy"><div class="firm">RIDGELINE ACCOUNTING &amp; CONSULTING, LLC</div>is a full-service Tax Firm firm licensed in VA. We offer a broad range of services for business owners, executives, and independent professionals. We are affordable, experienced, and friendly.</div>
    <div class="abs mess-title"><div class="r">Books a Mess:</div><div class="b">No Problem!</div></div>
    <div class="dotted" style="left:36px;top:222px;width:262px"></div>
    <div class="abs mess-copy body-copy">If you own a small business and haven’t kept up your bookkeeping, don’t worry. We can help you. We’ll prepare your bookkeeping for the year, prepare a full Schedule C, as well as your personal income tax return. Then we’ll help you set up an easy system that allows you to keep your books in tip-top shape next year.</div>
    <svg class="photo" style="left:0;top:390px" width="380" height="492" viewBox="0 0 380 492">
      <defs><linearGradient id="deskGrad" x1="0" y1="0" x2="1" y2="1"><stop offset="0" stop-color="#e9e4dc"/><stop offset=".6" stop-color="#c9ccd6"/><stop offset="1" stop-color="#9fb1d3"/></linearGradient></defs>
      <circle cx="30" cy="262" r="370" fill="none" stroke="var(--blue)" stroke-width="9"/>
      <circle cx="20" cy="262" r="360" fill="url(#deskGrad)" role="img" aria-label="Hands working with a calculator, pen and financial charts on a desk"/>
    </svg>
  </div>

  <!-- Contact panel -->
  <div class="panel panel--contact">
    <div class="photo" role="img" aria-label="Close-up of a calculator keypad over printed figures" style="left:0;top:0;width:380px;height:320px;background:linear-gradient(180deg,#b9bcc2 0%,#dcdee2 55%,#fff 100%)"></div>
    <svg class="abs" style="left:101px;top:281px" width="176" height="176"><circle cx="88" cy="88" r="84" fill="var(--blue)"/></svg>
    <div class="abs contact-head">Contact <span>Us</span></div>
    <div class="dotted" style="left:58px;top:551px;width:264px"></div>
    <div class="abs contact-icons">
      <svg width="34" height="34" viewBox="0 0 34 34"><circle cx="17" cy="17" r="15" fill="none" stroke="var(--red)" stroke-width="1.6"/><path d="M17 9a5 5 0 0 0-5 5c0 4 5 10 5 10s5-6 5-10a5 5 0 0 0-5-5z" fill="none" stroke="var(--blue)" stroke-width="1.6"/><circle cx="17" cy="14" r="1.8" fill="var(--blue)"/></svg>
      <svg width="34" height="34" viewBox="0 0 34 34"><circle cx="17" cy="17" r="15" fill="none" stroke="var(--red)" stroke-width="1.6"/><path d="M12 10l3 0 1.5 4-2 1.5a9 9 0 0 0 4 4l1.5-2 4 1.5v3c0 1-1 2-2 2-7 0-12-5-12-12 0-1 1-2 2-2z" fill="none" stroke="var(--blue)" stroke-width="1.6"/></svg>
      <svg width="34" height="34" viewBox="0 0 34 34"><circle cx="17" cy="17" r="15" fill="none" stroke="var(--red)" stroke-width="1.6"/><rect x="10" y="12" width="14" height="10" fill="none" stroke="var(--blue)" stroke-width="1.6"/><path d="M10 12l7 6 7-6" fill="none" stroke="var(--blue)" stroke-width="1.6"/></svg>
      <svg width="34" height="34" viewBox="0 0 34 34"><circle cx="17" cy="17" r="15" fill="none" stroke="var(--red)" stroke-width="1.6"/><circle cx="17" cy="17" r="8" fill="none" stroke="var(--blue)" stroke-width="1.6"/><ellipse cx="17" cy="17" rx="3.5" ry="8" fill="none" stroke="var(--blue)" stroke-width="1.4"/><path d="M9 17h16" stroke="var(--blue)" stroke-width="1.4"/></svg>
    </div>
    <div class="abs contact-firm">RIDGELINE ACCOUNTING &amp; CONSULTING, LLC</div>
    <div class="abs contact-line" style="top:654px;line-height:1.25">2280 Meadowbrook Rd, PO Box 14<br>Linden, VA 22642</div>
    <div class="abs contact-line contact-phone" style="top:702px">(555)014-2290</div>
    <div class="abs contact-line" style="top:742px">info@ridgelineacct.com</div>
    <div class="abs contact-line" style="top:780px">www.ridgelineacct.com</div>
    <div class="abs social"><i></i><i></i><i></i></div>
  </div>

  <!-- Cover panel -->
  <div class="panel panel--cover">
    <div class="abs brand"><div class="brand-dot"></div><div class="brand-name">RIDGELINE<small>CONSULTING, LLC</small></div></div>
    <div class="photo" role="img" aria-label="Hand with pen using a calculator over tax forms" style="left:0;top:185px;width:380px;height:400px;background:linear-gradient(160deg,#2c4f86 0%,#7d8fb0 40%,#d9dbe0 75%,#b9a98f 100%)"></div>
    <svg class="abs" style="left:0;top:145px" width="380" height="100" viewBox="0 0 380 100">
      <path d="M0 60 C110 10 260 0 380 30 L380 52 C260 26 120 38 0 76Z" fill="var(--blue)"/>
      <path d="M0 76 C120 38 260 26 380 52 L380 72 C260 50 120 62 0 96Z" fill="var(--red)"/>
    </svg>
    <svg class="abs" style="left:0;top:560px" width="380" height="90" viewBox="0 0 380 90">
      <path d="M0 40 C120 10 260 0 380 30 L380 50 C260 24 120 36 0 60Z" fill="var(--red)"/>
      <path d="M0 60 C120 36 260 24 380 50 L380 60 C260 40 120 50 0 72Z" fill="var(--blue)"/>
      <path d="M0 72 C120 50 260 40 380 60 L380 90 L0 90Z" fill="#fff"/>
    </svg>
    <div class="abs headline">OVER YOUR HEAD<br>IN PAPERWORK?<br><span class="red">WE CAN HELP YOU</span></div>
    <div class="abs tagline">Accounting and Tax Preparation<br>For Your Business</div>
    <div class="abs call-box">CALL: (555)014-2290</div>
  </div>
</section>

<!-- INSIDE SPREAD -->
<section class="spread spread--inside">
  <!-- Principal panel -->
  <div class="panel panel--principal">
    <div class="abs portrait" role="img" aria-label="Portrait of the firm principal" style="background:linear-gradient(160deg,#c9a27e,#6f5a4c)"></div>
    <div class="abs person-name">Marian T Hollis<small>MSA EA (Principal)</small></div>
    <div class="abs bio-wrap body-copy">
      <div class="gap"></div>
      <p>I have a Masters’ Degree in accounting and am an QFB Enrolled Agent. I am also a LedgerBooks Advanced Certified Consultant in both the online and desktop products including Enterprise and Point of Sale. I provide individual and small business tax services, Accounting, bookkeeping, QFB representation, insurance audit representation, business license assistance and more.</p>
      <p style="margin-top:16px">I have experience working with a wide variety of clients from the point where they first decide they want to start a business. They are often unsure about what to do first- I have a lot of experience to offer you.</p>
    </div>
    <div class="abs joy">What a joy it is to watch<br>success in action!</div>
    <div class="photo" role="img" aria-label="Young woman reviewing documents beside stacked binders in an office" style="left:0;top:535px;width:380px;height:347px;background:linear-gradient(135deg,#1d3f7f 0%,#3e6cb1 50%,#8aa9d6 100%)"></div>
    <svg class="abs" style="left:0;top:495px" width="380" height="80" viewBox="0 0 380 80">
      <path d="M0 30 C120 0 280 0 380 20 L380 36 C280 18 120 18 0 48Z" fill="var(--blue)"/>
      <path d="M0 48 C120 18 280 18 380 36 L380 52 C280 36 120 36 0 62Z" fill="var(--red)"/>
      <path d="M0 62 C120 36 280 36 380 52 L380 40 L380 0 L0 0Z" fill="none"/>
    </svg>
  </div>

  <!-- Why hire panel -->
  <div class="panel panel--why">
    <div class="abs kicker">Tax Preparation</div>
    <div class="abs why-title">Why Hire Us?</div>
    <div class="dotted" style="left:30px;top:120px;width:120px;border-color:#fff"></div>
    <div class="abs why-copy body-copy">
      <p>Preparing your own income tax return can be a task that leaves you with more questions than answers. According to a study released by the National Audit Bureau last year, most taxpayers (77% of 71 million taxpayers) believe they benefited from using a professional tax preparer.</p>
      <p>Whether we like it or not, today’s tax laws are so complicated that filing a relatively simple return can be confusing. It is just too easy to overlook deductions and credits to which you are entitled. Even if you use a computer software program there’s no substitute for the assistance of an experienced tax professional.</p>
    </div>
    <div class="abs services-head">Our Services</div>
    <div class="dotted" style="left:30px;top:464px;width:300px;border-color:#fff"></div>
    <div class="abs service" style="top:512px"><h3><svg width="30" height="30" viewBox="0 0 30 30"><rect x="3" y="6" width="24" height="20" rx="2" fill="none" stroke="var(--sky)" stroke-width="1.8"/><path d="M8 13h14M8 18h10" stroke="var(--sky)" stroke-width="1.8"/></svg>Tax Services</h3><p>We pride ourselves on being very efficient, affordable, and of course, extremely discreet.</p></div>
    <div class="abs service" style="top:628px"><h3><svg width="30" height="30" viewBox="0 0 30 30"><rect x="3" y="9" width="24" height="17" rx="2" fill="none" stroke="var(--sky)" stroke-width="1.8"/><path d="M11 9V5h8v4M3 16h24" stroke="var(--sky)" stroke-width="1.8" fill="none"/></svg>Business Services</h3><p>We take care of your business for you, so you can get back to the job of running your business.</p></div>
    <div class="abs service" style="top:736px"><h3><svg width="32" height="32" viewBox="0 0 32 32"><circle cx="16" cy="16" r="13" fill="none" stroke="var(--sky)" stroke-width="1.8" stroke-dasharray="4 2"/><circle cx="16" cy="13" r="4" fill="none" stroke="var(--sky)" stroke-width="1.8"/><path d="M9 24c2-4 12-4 14 0" fill="none" stroke="var(--sky)" stroke-width="1.8"/></svg>Services for Individuals</h3><p>You get one-on-one guidance that helps manage risk and improve performance.</p></div>
  </div>

  <!-- Benefits panel -->
  <div class="panel panel--gets">
    <svg class="abs" style="left:0;top:0" width="380" height="380" viewBox="0 0 380 380">
      <defs><linearGradient id="chartGrad" x1="0" y1="0" x2="1" y2="1"><stop offset="0" stop-color="#b9a48e"/><stop offset=".5" stop-color="#d9dde6"/><stop offset="1" stop-color="#8ea3c6"/></linearGradient></defs>
      <circle cx="300" cy="90" r="290" fill="none" stroke="var(--blue)" stroke-width="9"/>
      <circle cx="305" cy="85" r="282" fill="url(#chartGrad)" role="img" aria-label="Person analysing printed bar and pie charts beside a calculator"/>
    </svg>
    <div class="abs gets-head">Here’s what your get...</div>
    <div class="dotted" style="left:30px;top:454px;width:262px"></div>
    <div class="abs gets" style="top:484px"><svg width="34" height="38" viewBox="0 0 34 38"><rect x="3" y="3" width="22" height="30" fill="none" stroke="var(--red)" stroke-width="1.6"/><path d="M8 11h12M8 16h12M8 21h8" stroke="var(--red)" stroke-width="1.4"/><circle cx="24" cy="26" r="6" fill="#fff" stroke="var(--red)" stroke-width="1.6"/><path d="M28 30l4 4" stroke="var(--red)" stroke-width="1.6"/></svg><p><b>Your tax return will be checked and rechecked</b> by our computer software identifying potential problems the QFB may look at more closely and reviewing the math to limit QFB contacts.</p></div>
    <div class="abs gets" style="top:594px"><svg width="34" height="38" viewBox="0 0 34 38"><rect x="5" y="3" width="24" height="32" fill="none" stroke="var(--red)" stroke-width="1.6"/><path d="M10 11h14M10 16h14M10 21h14M10 26h9" stroke="var(--red)" stroke-width="1.4"/></svg><p><b>Your tax return can be filed electronically</b> so you will get a refund back quicker.</p></div>
    <div class="abs gets" style="top:672px"><svg width="34" height="38" viewBox="0 0 34 38"><circle cx="19" cy="15" r="11" fill="none" stroke="var(--red)" stroke-width="1.6"/><path d="M11 23l-8 10" stroke="var(--red)" stroke-width="2"/><path d="M14 15h10M19 10v10" stroke="var(--red)" stroke-width="1.4"/></svg><p><b>Our staff will show you how to adjust your payroll</b> withholding to get more money back each week. Why give the QFB an interest free loan for up to 16 months.</p></div>
    <div class="abs gets" style="top:766px"><svg width="34" height="38" viewBox="0 0 34 38"><rect x="3" y="6" width="22" height="28" fill="none" stroke="var(--red)" stroke-width="1.6"/><path d="M8 14h12M8 19h12M8 24h7" stroke="var(--red)" stroke-width="1.4"/><rect x="19" y="20" width="12" height="12" fill="#fff" stroke="var(--red)" stroke-width="1.6"/><path d="M22 26l3 3 4-6" fill="none" stroke="var(--red)" stroke-width="1.6"/></svg><p><b>We will show you potential deductions to limit your tax liability</b> for next year. In addition, we will give you a sheet of commonly overlooked deductions to limit the following year’s tax liability.</p></div>
  </div>
</section>

</body>
</html>
```